Brisk Fixwell business card

I need business card for my business, I think you have all my details.six months ago I design with you car wrap design. We would like to design both side of the card. On front of card we would like logo , Name and our contact details.
At the back we are looking to mentioned our services.
The name will be:
Faridoullan Mestor
Managing Director
Ph:07952338417
Email:info@brisk-fixwell.com
Web:www.brisk-fixwell.com
So we have our logo, you don’t need to change the logo.
Please see the attachment.
Thanks

Target Market(s)

Home improvement

Industry/Entity Type

Home Improvement

Contact Information for Business Card

Company name: Brisk Fixwell
Name: Faridoullan Mestor
Position: Director
Ph:07952338417
Web: www.brisk-fixwell.com
Add: 42 Corvale Road
Hounslow
TW3 9KD
SECOND PERSON
Nizamuddel mestor
Position: Handyman
Ph: 07812 564037
Email: info@brisk-fixwell.com
Add: 18 Brackwin Lane Road
Hounslow
TW6 2LB

```html
<!DOCTYPE html>
<html lang="en">
<head>
<meta charset="utf-8">
<title>Brisk Fixwell – Business Card</title>
<link href="https://fonts.googleapis.com/css2?family=Fira+Sans:wght@400;600;700&display=swap" rel="stylesheet">
<style>
  :root {
    --page-bg: #d9d6d2;
    --navy: #2c2f85;
    --navy-deep: #23266f;
    --red: #d7262b;
    --frost: #eceded;
    --frost-shade: #d6d8db;
    --text-light: #ffffff;
    --text-soft: #e3e4f2;
  }
  * { margin: 0; padding: 0; box-sizing: border-box; }
  html, body {
    width: 1200px; height: 1054px; overflow: hidden;
    background: var(--page-bg);
    font-family: "Fira Sans", Arial, sans-serif;
  }
  .card {
    position: absolute; left: 100px; top: 227px;
    width: 1000px; height: 600px;
    border-radius: 22px; overflow: hidden;
    background: linear-gradient(135deg, var(--frost) 0%, #f6f6f6 45%, var(--frost-shade) 100%);
    box-shadow: 0 18px 40px rgba(0,0,0,0.18);
  }
  .card-shapes { position: absolute; inset: 0; }
  .holder { position: absolute; left: 76px; top: 112px; color: var(--text-light); }
  .holder-name { font-size: 34px; font-weight: 600; letter-spacing: 0.2px; }
  .holder-role { font-size: 25px; font-weight: 400; color: var(--text-soft); margin-top: 8px; }
  .contact-list { position: absolute; left: 76px; top: 372px; list-style: none; }
  .contact-item {
    display: flex; align-items: center; height: 38px;
    font-size: 24px; color: var(--text-soft);
  }
  .contact-icon { width: 20px; height: 20px; margin-right: 29px; flex: none; }
  .brand {
    position: absolute; left: 810px; top: 300px;
    transform: translate(-50%, -50%) rotate(-90deg);
    display: flex; align-items: center; gap: 22px;
    white-space: nowrap;
  }
  .brand-name { font-size: 66px; font-weight: 700; color: var(--navy); letter-spacing: 1px; }
  .brand-mark { width: 58px; height: 58px; background: var(--navy); }
</style>
</head>
<body>
  <div class="card">
    <svg class="card-shapes" width="1000" height="600" viewBox="0 0 1000 600">
      <defs>
        <linearGradient id="panelShade" x1="0" y1="0" x2="1" y2="1">
          <stop offset="0" stop-color="#2f338c"/>
          <stop offset="1" stop-color="#23266f"/>
        </linearGradient>
      </defs>
      <path class="accent-curve" d="M0 0 H658 Q560 300 655 600 H0 Z" fill="var(--red)"/>
      <path class="navy-panel" d="M0 0 H646 Q548 300 643 600 H0 Z" fill="url(#panelShade)"/>
    </svg>

    <div class="holder">
      <div class="holder-name">Faridoullan Mestor</div>
      <div class="holder-role">Managing Director</div>
    </div>

    <ul class="contact-list">
      <li class="contact-item">
        <svg class="contact-icon" viewBox="0 0 20 20"><path d="M2 7 Q10 1 18 7 L16 9 L13 7.5 V6 H7 V7.5 L4 9 Z M4 11 H16 V17 H4 Z" fill="var(--red)"/></svg>
        07952338417
      </li>
      <li class="contact-item">
        <svg class="contact-icon" viewBox="0 0 20 20"><rect x="1" y="4" width="18" height="12" fill="var(--red)"/><path d="M1 4 L10 11 L19 4" fill="none" stroke="var(--navy)" stroke-width="1.6"/></svg>
        info@brisk-fixwell.com
      </li>
      <li class="contact-item">
        <svg class="contact-icon" viewBox="0 0 20 20"><circle cx="10" cy="10" r="8.5" fill="var(--red)"/><path d="M1.5 10 H18.5 M10 1.5 V18.5 M10 1.5 Q4 10 10 18.5 M10 1.5 Q16 10 10 18.5" fill="none" stroke="var(--navy)" stroke-width="1.2"/></svg>
        www.brisk-fixwell.com
      </li>
    </ul>

    <div class="brand">
      <span class="brand-name">Brisk Fixwell</span>
      <span class="brand-mark"></span>
    </div>
  </div>
</body>
</html>
```